Global (re)insurance broker needs a business card design

We need a classic business card for our company that is headquartered in SG, with offices in Malaysia and Dubai. We specialise in insurance and reinsurance broking and consultancy for our global clients.

```html
<!DOCTYPE html>
<html lang="en">
<head>
<meta charset="utf-8">
<title>Vantora Business Card</title>
<link href="https://fonts.googleapis.com/css2?family=Montserrat:wght@600&family=Open+Sans:wght@400;600&display=swap" rel="stylesheet">
<style>
  :root {
    --backdrop: #2b2b2e;
    --card: #151515;
    --brand-blue: #2a4aa0;
    --brand-mint: #c3dbb6;
    --ink-light: #f2f2f2;
  }
  * { box-sizing: border-box; margin: 0; padding: 0; }
  html, body { width: 1200px; height: 947px; overflow: hidden; }
  body {
    background: var(--backdrop);
    font-family: "Open Sans", sans-serif;
    display: flex;
    align-items: center;
    justify-content: center;
    gap: 40px;
  }
  .card {
    position: relative;
    width: 540px;
    height: 309px;
    background: var(--card);
    border-radius: 18px;
    box-shadow: 0 18px 40px rgba(0,0,0,0.45);
    overflow: hidden;
  }
  .wordmark {
    font-family: "Open Sans", sans-serif;
    font-weight: 600;
    color: var(--brand-mint);
    letter-spacing: 0.04em;
    line-height: 1;
  }
  .card--front {
    display: flex;
    align-items: center;
    justify-content: center;
  }
  .card--front .wordmark { font-size: 88px; }

  .card--back .wordmark {
    position: absolute;
    left: 36px;
    top: 58px;
    font-size: 54px;
  }
  .identity {
    position: absolute;
    right: 40px;
    top: 56px;
    text-align: right;
  }
  .identity__name {
    font-family: "Montserrat", sans-serif;
    font-weight: 600;
    font-size: 24px;
    color: var(--brand-blue);
  }
  .identity__title {
    font-size: 14px;
    color: var(--ink-light);
    margin-top: 4px;
  }
  .identity-bar {
    position: absolute;
    right: 0;
    top: 56px;
    width: 14px;
    height: 54px;
    background: var(--brand-blue);
  }
  .contact {
    position: absolute;
    left: 36px;
    bottom: 30px;
    color: var(--ink-light);
    font-size: 13px;
    line-height: 1.5;
  }
  .contact__address { margin-bottom: 8px; }
  .contact__line { display: flex; align-items: center; gap: 8px; }
  .contact__icon { width: 12px; height: 12px; fill: var(--brand-blue); flex: none; }
</style>
</head>
<body>
  <section class="card card--front" aria-label="Card front">
    <span class="wordmark">VANTORA</span>
  </section>

  <section class="card card--back" aria-label="Card back">
    <span class="wordmark">VANTORA</span>

    <div class="identity">
      <p class="identity__name">Mira Lowe</p>
      <p class="identity__title">Chief Operating Officer</p>
    </div>
    <div class="identity-bar"></div>

    <div class="contact">
      <p class="contact__address">22 Harbour Lane,<br>Meridian Tower #08-04,<br>Singapore 048812</p>
      <p class="contact__line">
        <svg class="contact__icon" viewBox="0 0 24 24" aria-hidden="true"><path d="M6.6 10.8a15.1 15.1 0 0 0 6.6 6.6l2.2-2.2c.3-.3.7-.4 1-.2 1.1.4 2.3.6 3.6.6.6 0 1 .4 1 1V20c0 .6-.4 1-1 1C10.6 21 3 13.4 3 4c0-.6.4-1 1-1h3.5c.6 0 1 .4 1 1 0 1.3.2 2.5.6 3.6.1.3 0 .7-.2 1z"/></svg>
        +65 6100 2345
      </p>
      <p class="contact__line">
        <svg class="contact__icon" viewBox="0 0 24 24" aria-hidden="true"><path d="M2 5h20v14H2z" fill="none"/><path d="M2 5h20v14H2V5zm2 2v.5l8 5 8-5V7H4z"/></svg>
        mira@vantora.com
      </p>
      <p class="contact__line">
        <svg class="contact__icon" viewBox="0 0 24 24" aria-hidden="true"><circle cx="12" cy="12" r="10"/><path d="M2 12h20M12 2c3 3 3 17 0 20M12 2c-3 3-3 17 0 20" stroke="#151515" stroke-width="1.5" fill="none"/></svg>
        www.vantora.com
      </p>
    </div>
  </section>
</body>
</html>
```